Dunmore Roofing

Want a professional looking business card

Industry/Entity Type

Business

Contact Information for Business Card

Paul Dunmore ( Owner) paul@dunmoreroofing-example.com, www.dunmoreroofing-example.com, Adress: 4172 Township road 43 Millbrook,NB K9X4T2

```html
<!DOCTYPE html>
<html lang="en">
<head>
<meta charset="utf-8">
<title>Dunmore Roofing – Business Card</title>
<link href="https://fonts.googleapis.com/css2?family=Open+Sans:wght@400;600;800&display=swap" rel="stylesheet">
<style>
  :root {
    --stage: #000000;
    --card: #2f3034;
    --brand-blue: #1f4c98;
    --text-light: #f2f2f2;
    --text-muted: #c9c9cc;
    --divider: #45464b;
  }
  * { margin: 0; padding: 0; box-sizing: border-box; }
  html, body {
    width: 1200px; height: 900px; overflow: hidden;
    background: var(--stage);
    font-family: "Open Sans", Arial, sans-serif;
  }
  .canvas { position: relative; width: 1200px; height: 900px; }
  .card {
    position: absolute; top: 271px;
    width: 457px; height: 281px;
    background: var(--card);
    border-radius: 14px;
    overflow: hidden;
  }
  .card--front { left: 137px; }
  .card--back { left: 626px; }

  .front-brand {
    position: absolute; left: 26px; top: 102px; width: 200px;
    color: var(--brand-blue); font-weight: 800;
    font-size: 30px; line-height: 1.02; letter-spacing: 0.5px;
    text-transform: uppercase;
  }
  .front-divider {
    position: absolute; left: 238px; top: 82px;
    width: 1px; height: 108px; background: var(--divider);
  }
  .contact {
    position: absolute; left: 256px; top: 82px;
    color: var(--text-light);
  }
  .contact__name { font-size: 15px; font-weight: 600; text-transform: uppercase; line-height: 20px; }
  .contact__role { font-size: 12px; color: var(--text-muted); line-height: 16px; }
  .contact__address { margin-top: 8px; font-size: 12px; line-height: 17px; }
  .contact__lines { margin-top: 5px; font-size: 10px; line-height: 17px; }
  .contact__line { display: flex; align-items: center; gap: 5px; white-space: nowrap; }
  .contact__line svg { width: 10px; height: 10px; flex: none; }

  .back-brand {
    position: absolute; left: 0; right: 0; top: 100px;
    text-align: center;
    color: var(--brand-blue); font-weight: 800;
    font-size: 40px; line-height: 1.05; letter-spacing: 2px;
    text-transform: uppercase;
  }
</style>
</head>
<body>
<main class="canvas">
  <section class="card card--front">
    <div class="front-brand">Dunmore<br>Roofing</div>
    <div class="front-divider"></div>
    <div class="contact">
      <p class="contact__name">Paul Dunmore</p>
      <p class="contact__role">Owner</p>
      <p class="contact__address">4172 Township road 43<br>Millbrook,NB K9X4T2</p>
      <div class="contact__lines">
        <p class="contact__line">
          <svg viewBox="0 0 10 10" aria-hidden="true"><rect x="0.5" y="2" width="9" height="6.5" fill="#f2f2f2"/><path d="M0.5 2 L5 5.6 L9.5 2" fill="none" stroke="#2f3034" stroke-width="1"/></svg>
          paul@dunmoreroofing-example.com
        </p>
        <p class="contact__line">
          <svg viewBox="0 0 10 10" aria-hidden="true"><circle cx="5" cy="5" r="4.5" fill="#f2f2f2"/><path d="M3 3.5 Q4.5 2.5 5 4 Q4 6 5.5 7.5 M6.5 2.5 Q7.5 4 6.8 5" fill="none" stroke="#2f3034" stroke-width="0.9"/></svg>
          www.dunmoreroofing-example.com
        </p>
      </div>
    </div>
  </section>

  <section class="card card--back">
    <div class="back-brand">Dunmore<br>Roofing</div>
  </section>
</main>
</body>
</html>
```